Beyond the Ember Line. A Survivor’s Guide to Rebuilding After Wildfire

I need a book cover for a book I will publish on Brixel Leafpad. It is a survivor's guide to rebuilding after wildfire

Target Market(s)

Homeowners whose homes burned in Los Angeles wildfires in January 2025

Industry/Entity Type

rebuilding after natural disaster

Font styles to use
Sans Serif

Colors

Designer to choose colors to be used in the design.

Requirements
Must have
• 1. Title: Beyond the Ember Line Should be bold and easy to read, even in thumbnail size. Consider a strong, resilient font with a modern, clean look. Subtitle: A Survivor’s Guide to Rebuilding After Wildfire Smaller than the title but still legible. 2. Imagery & Visual Concept Symbolism of Transformation & Rebuilding: A house rising from the ashes, partially rebuilt or fortified with fire-resistant features. A phoenix-like motif (metaphor for renewal) but with a focus on home resilience. Contrast Between Destruction & Recovery: One side of the image could depict a burned landscape (blackened trees, smoke, or embers in the air). The other side transitioning into a rebuilt, fire-resistant home, symbolizing hope and action. 3. Color Palette Warm tones (fire hues): Orange, red, and yellow to represent the wildfire’s destructive power. Cool, hopeful colors: Blue, green, or earthy tones to symbolize renewal, rebuilding, and resilience. Contrast: The colors should show before and after—destruction and recovery. 4. Texture & Mood A subtle gritty texture for realism, balanced with a clean, modern look for readability. Lighting: A soft glow from a rising sun to indicate a new beginning. 5. Author Name (Legible & Professional) Otto Varnsby Should be visible but secondary to the title. 6. Format Considerations Ensure design works in Brixel Leafpad (ebook), print, and thumbnail views.
Nice to have
• Human Element (Optional): A silhouette of a homeowner or a family standing strong in front of their rebuilding home. 2. Space for a Tagline (Optional) A short callout like: The Ultimate Step-by-Step Guide to Rebuilding After Wildfire
Should not have
• Avoid overly cluttered visuals—keep it clean, powerful, and easy to read.

```html
<!DOCTYPE html>
<html lang="en">
<head>
<meta charset="utf-8">
<title>Beyond the Ember Line – Book Cover Wrap</title>
<link href="https://fonts.googleapis.com/css2?family=Bebas+Neue&family=Montserrat:wght@400;600&display=swap" rel="stylesheet">
<style>
  :root {
    --paper: #ffffff;
    --cream: #f8f5ea;
    --amber: #f7b023;
    --ember-red: #c3202f;
    --ink: #231f20;
    --rule: #f08a1c;
  }
  * { margin: 0; padding: 0; box-sizing: border-box; }
  html, body { width: 1200px; height: 844px; overflow: hidden; background: var(--paper); }
  .wrap { position: relative; width: 1200px; height: 844px; }

  .back-cover {
    position: absolute; left: 22px; top: 22px; width: 622px; height: 800px;
    background: var(--cream);
  }
  .blurb {
    position: absolute; left: 49px; width: 436px;
    font-family: "Montserrat", sans-serif; font-size: 11.6px; line-height: 14.8px;
    color: var(--ink); text-align: justify; letter-spacing: -0.15px;
  }
  .blurb-top { top: 31px; }
  .blurb-bottom { top: 539px; }
  .author-badge {
    position: absolute; left: 195px; top: 385px; width: 146px; height: 146px;
    border: 2px solid var(--ember-red); border-radius: 50%;
  }
  .barcode-box {
    position: absolute; left: 307px; top: 656px; width: 187px; height: 98px;
    background: #ffffff;
  }

  .spine-title, .spine-author {
    position: absolute; writing-mode: vertical-rl; white-space: nowrap;
  }
  .spine-title {
    left: 558px; top: 31px;
    font-family: "Bebas Neue", sans-serif; font-size: 53px; line-height: 1;
    color: var(--ink);
  }
  .spine-title .accent { color: var(--ember-red); }
  .spine-author {
    left: 566px; top: 505px;
    font-family: "Montserrat", sans-serif; font-weight: 600; font-size: 29px; line-height: 1;
    color: var(--ink);
  }

  .front-cover {
    position: absolute; left: 644px; top: 22px; width: 534px; height: 800px;
    background: var(--amber);
  }
  .front-title { position: absolute; left: 38px; top: 28px; width: 460px; height: 212px; }
  .front-title text { font-family: "Bebas Neue", sans-serif; }
  .subtitle {
    position: absolute; left: 0; top: 259px; width: 534px; text-align: center;
    font-family: "Montserrat", sans-serif; font-weight: 600; font-size: 28.5px; line-height: 33px;
    color: var(--ink); letter-spacing: 0.6px;
  }
  .subtitle-rule {
    position: absolute; left: 67px; width: 400px; height: 1px; background: var(--rule);
  }
  .rule-top { top: 259px; }
  .rule-bottom { top: 336px; }
  .band { position: absolute; left: 0; width: 534px; height: 5px; background: var(--ember-red); }
  .band-top { top: 358px; }
  .band-bottom { top: 680px; }
  .cover-image {
    position: absolute; left: 0; top: 363px; width: 534px; height: 317px;
    background:
      linear-gradient(180deg, rgba(0,0,0,0) 82%, #3d5a2a 92%, #2e4420 100%),
      radial-gradient(ellipse 55% 60% at 58% 55%, #ff8a1e 0%, #e0531a 35%, rgba(60,40,35,0) 75%),
      linear-gradient(100deg, #c9cfd0 0%, #a7a49b 30%, #4a3a34 60%, #2a2422 100%);
  }
  .author {
    position: absolute; left: 0; top: 715px; width: 534px; text-align: center;
    font-family: "Montserrat", sans-serif; font-weight: 600; font-size: 40px; line-height: 1;
    color: var(--ink);
  }
</style>
</head>
<body>
<div class="wrap">
  <section class="back-cover">
    <p class="blurb blurb-top">Lorem ipsum dolor sit amet, consectetuer adipiscing elit, sed diam nonummy nibh euismod tincidunt ut laoreet dolore magna aliquam erat volutpat. Ut wisi enim ad minim veniam, quis nostrud exerci tation ullamcorper suscipit lobortis nisl ut aliquip ex ea commodo consequat. Duis autem vel eum iriure dolor in hendrerit in vulputate velit esse molestie consequat, vel illum dolore eu feugiat nulla facilisis at vero eros et accumsan et iusto odio dignissim qui blandit praesent luptatum zzril delenit augue duis dolore te feugait nulla facilisi.<br>Lorem ipsum dolor sit amet, cons ectetuer adipiscing elit, sed diam nonummy nibh euismod tincidunt ut laoreet dolore magna aliquam erat volutpat. Ut wisi enim ad minim veniam, quis nostrud exerci tation ullamcorper suscipit lobortis nisl ut aliquip ex ea commodo consequat.<br>Lorem ipsum dolor sit amet, consectetuer adipiscing elit, sed diam nonummy nibh euismod tincidunt ut laoreet dolore magna aliquam erat volutpat. Ut wisi enim ad minim veniam, quis nostrud exerci tation ullamcorper suscipit lobortis nisl ut aliquip ex ea commodo consequat. Duis autem vel eum iriure dolor in hendrerit in vulputate velit esse molestie consequat, vel illum dolore eu feugiat nulla facilisis at vero eros et accumsan et iusto odio dignissim qui blandit praesent luptatum zzril delenit augue duis dolore te feugait nulla facilisi.<br>Lorem ipsum dolor sit amet, cons ectetuer adipiscing elit, sed diam nonummy nibh euismod tincidunt ut laoreet dolore magna aliquam erat volutpat. Ut wisi enim ad minim veniam, quis nostrud exerci tation ullamcorper suscipit lobortis nisl ut aliquip ex ea commodo consequat.</p>
    <div class="author-badge"></div>
    <p class="blurb blurb-bottom">Lorem ipsum dolor sit amet, consectetuer adipiscing elit, sed diam nonummy nibh euismod tincidunt ut laoreet dolore magna aliquam erat volutpat. Ut wisi enim ad minim veniam, quis nostrud exerci tation ullamcorper suscipit lobortis nisl ut aliquip ex ea commodo consequat. Duis autem vel eum iriure dolor in hendrerit in vulputate velit esse molestie consequat, vel illum dolore eu feugiat nulla facilisis at vero eros et accumsan et iusto odio dignissim qui blandit praesent luptatum</p>
    <div class="barcode-box"></div>
    <div class="spine-title"><span class="accent">BEYOND THE</span> EMBER LINE</div>
    <div class="spine-author">Otto Varnsby</div>
  </section>

  <section class="front-cover">
    <svg class="front-title" viewBox="0 0 460 212" aria-label="Beyond the Ember Line">
      <text x="0" y="88" font-size="126" fill="var(--ember-red)" textLength="458" lengthAdjust="spacingAndGlyphs">BEYOND THE</text>
      <text x="0" y="206" font-size="152" fill="var(--ink)" textLength="458" lengthAdjust="spacingAndGlyphs">EMBER LINE</text>
    </svg>
    <div class="subtitle-rule rule-top"></div>
    <p class="subtitle">A Survivor’s Guide to<br>Rebuilding After Wildfire</p>
    <div class="subtitle-rule rule-bottom"></div>
    <div class="band band-top"></div>
    <div class="cover-image" role="img" aria-label="Photograph of a two-storey house engulfed in flames with dark smoke against a pale sky, on a green lawn"></div>
    <div class="band band-bottom"></div>
    <p class="author">Otto Varnsby</p>
  </section>
</div>
</body>
</html>
```